Online business manager needs a website

I need a website designed and then coded. I am an online business manager serving a number of different industries providing administrative support to existing small businesses and helping solo practitioners get their new business up and running.

I didn't have a logo formally designed but have been using the attached avatar and wouldn't mind something that incorporated that.

The business doesn't have an official name, so I've just been using my name Lena Morvath, Online Business Manager or Lena Morvath, OBM. I've attached two documents that I have made previously for an example of content.

I would prefer the final site be in Wordpress.

Requirements
Must have
• A way to contact me, testimonials, list of services

```html
<!DOCTYPE html>
<html lang="en">
<head>
<meta charset="UTF-8">
<title>Lena Morvath – Online Business Manager</title>
<link rel="stylesheet" href="https://fonts.googleapis.com/css2?family=Pacifico&family=Poppins:wght@400;500;600;700&display=swap">
<style>
:root{
  --purple:#4b1780;
  --purple-soft:#b9a3d8;
  --lavender:#f3eefb;
  --ink:#2b2b2b;
  --text:#666;
  --white:#fff;
  --footer:#2b2b2b;
  --gold:#f2b500;
}
*{box-sizing:border-box;margin:0;padding:0}
html,body{width:1200px;height:4950px;overflow:hidden}
body{font-family:'Poppins',sans-serif;color:var(--ink);background:var(--white);position:relative}
.abs{position:absolute}
.script{font-family:'Pacifico',cursive;font-weight:400}

/* header */
.site-header{position:absolute;left:0;top:0;width:1200px;height:145px}
.brand{position:absolute;left:112px;top:28px}
.brand-name{font-family:'Pacifico',cursive;color:var(--purple);font-size:34px;line-height:1.1}
.brand-tag{font-size:15px;letter-spacing:3px;margin-top:6px;color:var(--ink)}
.main-nav{position:absolute;left:452px;top:64px;display:flex;gap:24px;font-size:14px;font-weight:500}
.main-nav a{color:var(--ink);text-decoration:none}
.main-nav a.active{color:var(--purple)}
.call{position:absolute;left:902px;top:50px;display:flex;align-items:center;gap:18px}
.call-icon{width:42px;height:42px;background:var(--purple);border-radius:4px;display:flex;align-items:center;justify-content:center}
.call small{display:block;font-size:10px;font-weight:600;color:var(--ink)}
.call strong{display:block;font-size:19px;font-weight:600;color:var(--purple)}

/* hero */
.hero-photo{left:0;top:145px;width:686px;height:565px;background:linear-gradient(120deg,#c9b59a,#8a6a4a 55%,#e0c8a8)}
.hero-panel{left:600px;top:187px;width:600px;height:481px;background:var(--purple);color:var(--white);padding:62px 62px}
.hero-panel h1{font-family:'Pacifico',cursive;font-weight:400;font-size:46px;line-height:1.2}
.hero-panel h2{font-weight:500;font-size:26px;letter-spacing:1px;margin-top:12px}
.hero-panel p{font-size:18px;line-height:1.65;margin-top:18px}
.btn-light{display:inline-block;background:var(--white);color:var(--ink);font-size:14px;font-weight:500;padding:14px 22px;border-radius:3px;margin-top:26px}
.hero-social{display:flex;align-items:center;gap:26px;margin-top:52px}
.dot{width:12px;height:12px;border-radius:50%;background:var(--white)}
.hero-social .line{width:62px;height:2px;background:var(--white);margin-left:14px}

/* headings */
.section-title{position:absolute;left:0;width:1200px;text-align:center;font-family:'Pacifico',cursive;font-size:54px;color:var(--ink)}
.section-title .accent{color:var(--purple)}

/* services */
.service-photo{width:471px;height:342px;position:absolute}
.service-label{position:absolute;width:410px;height:118px;background:var(--white);box-shadow:0 6px 18px rgba(0,0,0,.12);display:flex;align-items:center;justify-content:center;text-align:center;font-size:20px;font-weight:500;line-height:1.45}

/* about */
.about-band{left:0;top:1892px;width:1200px;height:498px;background:var(--lavender)}
.about-ring{left:112px;top:1944px;width:394px;height:394px;border-radius:50%;border:4px solid var(--purple-soft)}
.about-photo{left:112px;top:1944px;width:394px;height:394px;border-radius:50%;background:radial-gradient(circle at 50% 55%,#d8a870,#3a2a6a 70%,#1a1240)}
.about-text{left:600px;top:1950px;width:488px}
.about-text h2{font-family:'Pacifico',cursive;font-weight:400;font-size:54px}
.about-text p{font-size:15px;color:var(--text);line-height:1.78;margin-top:18px;text-align:justify}
.btn-purple{display:inline-block;background:var(--purple);color:var(--white);font-size:14px;font-weight:600;padding:15px 26px;border-radius:3px;margin-top:36px}

/* best */
.best-photo{left:505px;top:2390px;width:695px;height:480px;background:linear-gradient(130deg,#dfe7ee,#8ea6bb 50%,#3a4a6a)}
.best-panel{left:110px;top:2462px;width:487px;height:480px;background:var(--purple);color:var(--white);padding:60px 68px}
.best-panel h2{font-family:'Pacifico',cursive;font-weight:400;font-size:36px}
.best-list{list-style:none;margin-top:22px}
.best-list li{display:flex;align-items:center;gap:30px;font-size:17px;height:34.3px}

/* rates */
.rate{position:absolute;top:3155px;width:231px;height:250px;background:var(--white);box-shadow:0 4px 16px rgba(0,0,0,.12);border-radius:4px;text-align:center;padding-top:30px}
.rate.featured{border:3px solid var(--purple);padding-top:27px}
.rate .price{font-size:26px;font-weight:600;color:var(--purple)}
.rate .term{font-size:16px;font-weight:600;margin-top:10px}
.rate p{font-size:14px;color:var(--text);line-height:1.7;margin-top:14px;padding:0 30px}

/* testimonials */
.testi-band{left:0;top:3538px;width:1200px;height:472px;background:linear-gradient(135deg,#f6f2fb,#ece4f6 50%,#f6f2fb)}
.testi-avatar{left:555px;top:3692px;width:90px;height:90px;border-radius:50%;border:4px solid var(--white);background:linear-gradient(140deg,#e8b08a,#8a5a6a);box-shadow:0 2px 8px rgba(0,0,0,.15)}
.testi-quote{left:160px;top:3812px;width:880px;text-align:center;font-size:16px;line-height:1.7;color:#555}
.testi-name{left:0;top:3906px;width:1200px;text-align:center;font-size:14px}
.testi-name b{color:var(--purple);font-weight:600}
.stars{left:0;top:3936px;width:1200px;text-align:center;color:var(--gold);font-size:14px;letter-spacing:2px}

/* contact */
.info{position:absolute;top:4200px;display:flex;align-items:center;gap:24px}
.info-icon{width:70px;height:70px;border-radius:50%;background:var(--white);box-shadow:0 4px 14px rgba(0,0,0,.12);display:flex;align-items:center;justify-content:center}
.info b{display:block;font-size:13px;font-weight:600}
.info span{display:block;font-size:13px;color:var(--text);line-height:1.5;margin-top:6px}
.field{position:absolute;height:48px;background:var(--white);box-shadow:0 2px 10px rgba(0,0,0,.1);font-size:14px;color:#777;padding:14px 18px}
.send{left:518px;top:4490px;width:164px;height:48px;background:var(--purple);color:var(--white);font-size:14px;font-weight:600;display:flex;align-items:center;justify-content:center;border-radius:2px}

/* footer */
.site-footer{left:0;top:4615px;width:1200px;height:335px;background:var(--footer);color:var(--white);text-align:center}
.site-footer .brand-name{color:var(--white);font-size:34px;margin-top:36px}
.site-footer .brand-tag{color:var(--white);font-size:16px;letter-spacing:3px}
.foot-nav{display:flex;justify-content:center;gap:30px;font-size:16px;font-weight:600;margin-top:28px}
.foot-contact{display:flex;justify-content:center;align-items:center;gap:18px;font-size:15px;margin-top:22px}
.foot-social{display:flex;justify-content:center;gap:10px;margin-top:18px}
.foot-social span{width:34px;height:34px;border-radius:50%;border:1.5px solid var(--white);display:flex;align-items:center;justify-content:center}
.foot-social span:first-child{background:var(--white)}
.foot-rule{width:976px;height:1px;background:#555;margin:18px auto 0}
.copy{font-size:12px;margin-top:16px}
</style>
</head>
<body>

<header class="site-header">
  <div class="brand">
    <div class="brand-name">Lena Morvath</div>
    <div class="brand-tag">ONLINE BUSINESS MANAGER</div>
  </div>
  <nav class="main-nav">
    <a class="active" href="#">HOME</a><a href="#">ABOUT ME</a><a href="#">SERVICES</a><a href="#">PRICING</a><a href="#">CONTACT</a>
  </nav>
  <div class="call">
    <div class="call-icon"><svg width="18" height="18" viewBox="0 0 24 24"><path fill="#fff" d="M6.6 10.8a15 15 0 0 0 6.6 6.6l2.2-2.2c.3-.3.7-.4 1-.2 1.1.4 2.3.6 3.6.6.6 0 1 .4 1 1V20c0 .6-.4 1-1 1A17 17 0 0 1 3 4c0-.6.4-1 1-1h3.5c.6 0 1 .4 1 1 0 1.3.2 2.5.6 3.6.1.3 0 .7-.2 1z"/></svg></div>
    <div><small>CALL US:</small><strong>555.210.4837</strong></div>
  </div>
</header>

<div class="abs hero-photo" role="img" aria-label="Photo of a smiling woman working on a laptop at a wooden desk"></div>
<section class="abs hero-panel">
  <h1>Lena Morvath</h1>
  <h2>Online Business Manager</h2>
  <p>Focused on the live event and entertainment industry. Helping artists and owners to better manage their career and business</p>
  <span class="btn-light">GET STARTED</span>
  <div class="hero-social" aria-label="Social links"><span class="dot"></span><span class="dot"></span><span class="dot"></span><span class="line"></span></div>
</section>

<h2 class="section-title" style="top:800px">Services</h2>
<div class="service-photo" style="left:112px;top:918px;background:linear-gradient(135deg,#d8dde4,#6e7888 60%,#3a3f4a)" role="img" aria-label="Photo of hands typing on a laptop with floating app icons"></div>
<div class="service-label" style="left:142px;top:1202px">Virtual Assistance</div>
<div class="service-photo" style="left:617px;top:918px;background:linear-gradient(135deg,#6a5a4a,#c8a888 55%,#e8d8c4)" role="img" aria-label="Photo of a team reviewing sticky notes on a glass wall"></div>
<div class="service-label" style="left:647px;top:1202px">Social Media &amp; Content<br>Management</div>
<div class="service-photo" style="left:112px;top:1358px;background:linear-gradient(135deg,#f0f0f0,#bfc7cc 55%,#6a6a6a)" role="img" aria-label="Photo of financial reports and charts on a desk"></div>
<div class="service-label" style="left:142px;top:1640px">Finance Management</div>
<div class="service-photo" style="left:617px;top:1358px;background:linear-gradient(135deg,#3a3f55,#8a6a78 55%,#d0b0a8)" role="img" aria-label="Photo of hands on a laptop with floating folder icons"></div>
<div class="service-label" style="left:647px;top:1640px">Business Management</div>

<div class="abs about-band"></div>
<div class="abs about-ring" style="left:124px;top:1934px"></div>
<div class="abs about-photo" role="img" aria-label="Portrait photo of the business manager"></div>
<div class="abs about-text">
  <h2>About Me</h2>
  <p>Hi! I'm so excited that you have chosen to explore my portfolio. Helping businesses achieve their goals is my passion, and I'm thrilled that with my assistance you will have more time for your own passion project. I thrive while working independently, which means you can be confident when leaving tasks for me. The type of work that lights me up is anything involving organization and/or spreadsheets.</p>
  <span class="btn-purple">READ MORE</span>
</div>

<div class="abs best-photo" role="img" aria-label="Photo of two colleagues smiling at a computer in an office"></div>
<section class="abs best-panel">
  <h2>What I Do Best</h2>
  <ul class="best-list">
    <li><svg width="16" height="16" viewBox="0 0 16 16"><circle cx="8" cy="8" r="8" fill="#fff"/><path d="M6 4.5 9.5 8 6 11.5" stroke="#4b1780" stroke-width="2" fill="none"/></svg>Content Repurposing</li>
    <li><svg width="16" height="16" viewBox="0 0 16 16"><circle cx="8" cy="8" r="8" fill="#fff"/><path d="M6 4.5 9.5 8 6 11.5" stroke="#4b1780" stroke-width="2" fill="none"/></svg>Data Entry</li>
    <li><svg width="16" height="16" viewBox="0 0 16 16"><circle cx="8" cy="8" r="8" fill="#fff"/><path d="M6 4.5 9.5 8 6 11.5" stroke="#4b1780" stroke-width="2" fill="none"/></svg>Email Management</li>
    <li><svg width="16" height="16" viewBox="0 0 16 16"><circle cx="8" cy="8" r="8" fill="#fff"/><path d="M6 4.5 9.5 8 6 11.5" stroke="#4b1780" stroke-width="2" fill="none"/></svg>Bookkeeping</li>
    <li><svg width="16" height="16" viewBox="0 0 16 16"><circle cx="8" cy="8" r="8" fill="#fff"/><path d="M6 4.5 9.5 8 6 11.5" stroke="#4b1780" stroke-width="2" fill="none"/></svg>Financial Analytics</li>
    <li><svg width="16" height="16" viewBox="0 0 16 16"><circle cx="8" cy="8" r="8" fill="#fff"/><path d="M6 4.5 9.5 8 6 11.5" stroke="#4b1780" stroke-width="2" fill="none"/></svg>Graphic Creations</li>
    <li><svg width="16" height="16" viewBox="0 0 16 16"><circle cx="8" cy="8" r="8" fill="#fff"/><path d="M6 4.5 9.5 8 6 11.5" stroke="#4b1780" stroke-width="2" fill="none"/></svg>Project Management</li>
    <li><svg width="16" height="16" viewBox="0 0 16 16"><circle cx="8" cy="8" r="8" fill="#fff"/><path d="M6 4.5 9.5 8 6 11.5" stroke="#4b1780" stroke-width="2" fill="none"/></svg>More Awesomeness</li>
  </ul>
</section>

<h2 class="section-title" style="top:3040px;font-size:42px">Rates &amp; <span class="accent">Packages</span></h2>
<div class="rate" style="left:112px"><div class="price">$40</div><div class="term">HOURLY RATE</div><p>For clients needing only occasional help</p></div>
<div class="rate" style="left:360px"><div class="price">$700</div><div class="term">20 HOURS/MONTH</div><p>Includes one 15 minute meeting per week</p><p style="margin-top:8px">Responses within 72 hours</p></div>
<div class="rate featured" style="left:609px"><div class="price">$1,300</div><div class="term">40 HOURS/MONTH</div><p>Includes one 30 minute meeting per week</p><p style="margin-top:8px">Responses within 48 hours</p></div>
<div class="rate" style="left:857px"><div class="price">$2,400</div><div class="term">80 HOURS/MONTH</div><p>Includes one 60 minute meeting per week</p><p style="margin-top:8px">Responses within 24 hours</p></div>

<div class="abs testi-band"></div>
<h2 class="section-title" style="top:3585px">Testimonials</h2>
<div class="abs testi-avatar" role="img" aria-label="Client profile photo"></div>
<p class="abs testi-quote">When it became apparent that a project would take more time than I had, Lena stepped up to take on the required research. She was thorough and timely; able to meet a last-minute 12-hour deadline. I would highly recommend Lena to assist with your next project.</p>
<p class="abs testi-name"><b>– DANA R. OWNER,</b> Ridgeline Roofing</p>
<div class="abs stars">★★★★★</div>

<h2 class="section-title" style="top:4090px">Contact <span class="accent">Me</span></h2>
<div class="info" style="left:198px">
  <div class="info-icon"><svg width="24" height="24" viewBox="0 0 24 24"><path d="M12 2a6 6 0 0 0-6 6c0 4.5 6 11 6 11s6-6.5 6-11a6 6 0 0 0-6-6zm0 8.5A2.5 2.5 0 1 1 12 5.5a2.5 2.5 0 0 1 0 5z" fill="#4b1780"/><path d="M4 21h16" stroke="#4b1780" stroke-width="2"/></svg></div>
  <div><b>LOCATION:</b><span>Millbrook, Oregon,<br>United States</span></div>
</div>
<div class="info" style="left:492px;top:4210px">
  <div class="info-icon"><svg width="24" height="24" viewBox="0 0 24 24"><path fill="#4b1780" d="M6.6 10.8a15 15 0 0 0 6.6 6.6l2.2-2.2c.3-.3.7-.4 1-.2 1.1.4 2.3.6 3.6.6.6 0 1 .4 1 1V20c0 .6-.4 1-1 1A17 17 0 0 1 3 4c0-.6.4-1 1-1h3.5c.6 0 1 .4 1 1 0 1.3.2 2.5.6 3.6.1.3 0 .7-.2 1z"/></svg></div>
  <div><b>PHONE:</b><span>555.210.4837</span></div>
</div>
<div class="info" style="left:724px;top:4210px">
  <div class="info-icon"><svg width="24" height="24" viewBox="0 0 24 24"><rect x="3" y="6" width="18" height="13" rx="1.5" fill="#4b1780"/><path d="M3.5 7 12 13l8.5-6" stroke="#fff" stroke-width="1.6" fill="none"/></svg></div>
  <div><b>EMAIL ADDRESS:</b><span>hello@lenamorvath.example</span></div>
</div>
<div class="field" style="left:165px;top:4298px;width:283px">Full Name</div>
<div class="field" style="left:458px;top:4298px;width:282px">Phone Number</div>
<div class="field" style="left:750px;top:4298px;width:284px">Email Address</div>
<div class="field" style="left:165px;top:4360px;width:869px;height:92px">Message...!</div>
<div class="abs send">SEND MESSAGE</div>

<footer class="abs site-footer">
  <div class="brand-name">Lena Morvath</div>
  <div class="brand-tag">ONLINE BUSINESS MANAGER</div>
  <nav class="foot-nav"><span>HOME</span><span>|</span><span>ABOUT ME</span><span>|</span><span>SERVICES</span><span>|</span><span>PRICING</span><span>|</span><span>CONTACT</span></nav>
  <div class="foot-contact"><span>☎ 555.210.4837</span><span>|</span><span>✉ hello@lenamorvath.example</span></div>
  <div class="foot-social" aria-label="Social links"><span></span><span></span><span></span></div>
  <div class="foot-rule"></div>
  <p class="copy">Copyright © 2023 Lena Morvath Online Business Manager All Rights Reserved</p>
</footer>

</body>
</html>
```